Satchel & Sundial needs new business card design

I need a new business card design. I'm looking for out-of-the-box design which represents the freedom of being a location independent entrepreneur.
I offer coaching, retreats and trips.
I would like to see designs with and without the photo.
Colors I use are black (#000000), green (#25A796) and brown (#D7C38C)
Website satchelandsundial.example

Target Market(s)

location independent entrepreneurs, digital nomads, people looking to swap the 9 to 5 for a lifestyle business

Industry/Entity Type

Business

Contact Information for Business Card

Dorota Falkner
Your Lifestyle Business Coach, Retreat & Trip Leader
http://satchelandsundial.example
hello@satchelandsundial.example
Live a life you don't need a holiday from

Font styles to use
Serif
Sans Serif

Requirements
Must have
• One side should contain only the logo. I would also consider having the "Live a life you don't need a holiday from" on that side too (depending on how it looks)
• Please show both sides on the designs.

```html
<!DOCTYPE html>
<html lang="en">
<head>
<meta charset="utf-8">
<title>Satchel &amp; Sundial — Business Cards</title>
<link rel="stylesheet" href="https://fonts.googleapis.com/css2?family=Arimo:wght@400;700&display=swap">
<style>
  :root {
    --ink: #1e1e1e;
    --ink-soft: #333333;
    --teal: #3fc1b0;
    --card: #ffffff;
    --stage: #e9e7e2;
    --rock-dark: #b9b9b6;
    --rock-light: #e4e4e2;
  }
  * { box-sizing: border-box; margin: 0; padding: 0; }
  html, body {
    width: 1200px; height: 858px; overflow: hidden;
    background: var(--stage);
    font-family: "Arimo", Arial, sans-serif;
  }
  .sheet {
    width: 1200px; height: 858px;
    display: flex; align-items: center; justify-content: center; gap: 32px;
  }
  .card {
    position: relative;
    width: 560px; height: 320px;
    background: var(--card);
    overflow: hidden;
    box-shadow: 0 2px 10px rgba(0,0,0,0.12);
  }
  .wordmark {
    font-weight: 700;
    color: var(--ink);
    text-transform: uppercase;
    letter-spacing: 0.04em;
    line-height: 1;
  }
  /* Front */
  .card--front .wordmark {
    position: absolute; left: 0; right: 0; top: 112px;
    text-align: center; font-size: 40px;
  }
  .card--front .tagline {
    position: absolute; left: 0; right: 0; top: 206px;
    text-align: center; font-size: 16px; color: var(--ink-soft);
  }
  /* Back */
  .card__photo {
    position: absolute; left: 0; top: 0; width: 62%; height: 100%;
    background:
      linear-gradient(90deg, rgba(255,255,255,0) 55%, var(--card) 100%),
      linear-gradient(160deg, var(--rock-light) 0%, var(--rock-dark) 45%, var(--rock-light) 80%);
    opacity: 0.85;
  }
  .card--back .wordmark {
    position: absolute; right: 34px; top: 40px;
    font-size: 28px; text-align: right;
  }
  .identity {
    position: absolute; left: 196px; top: 118px;
  }
  .identity__name {
    font-weight: 700; font-size: 22px; color: var(--ink);
    margin-bottom: 8px;
  }
  .identity__role {
    font-size: 14px; color: var(--teal); line-height: 1.35;
  }
  .contact {
    position: absolute; left: 34px; bottom: 36px;
    font-size: 13px; color: var(--ink); line-height: 1.6;
    list-style: none;
  }
</style>
</head>
<body>
<main class="sheet">
  <section class="card card--front" aria-label="Card front">
    <div class="wordmark">Satchel &amp; Sundial</div>
    <p class="tagline">Live a life you don't need a holiday from</p>
  </section>

  <section class="card card--back" aria-label="Card back">
    <div class="card__photo" role="img" aria-label="Faded grey photograph of a rocky coastal cliff"></div>
    <div class="wordmark">Satchel &amp; Sundial</div>
    <div class="identity">
      <p class="identity__name">Dorota Falkner</p>
      <p class="identity__role">Your Lifestyle Business Coach,<br>Retreat &amp; Trip Leader</p>
    </div>
    <ul class="contact">
      <li>hello@satchelandsundial.example</li>
      <li>http://satchelandsundial.example</li>
    </ul>
  </section>
</main>
</body>
</html>
```